Advertising company unique advertising platform

we need a logo design for a new company based in Australia Melbourne. We develop innovated advertising platform where consumer can use this platform to get regular discount, as business owner they can use this platform for free advertisement. Payment for this advertisement platform only payable every two weeks, when I generate revenue for their business

Industry/Entity Type

Advertising

Contact Information for Business Card

Dale Morven | Co-Founder |Managing Director
Suite 718 240 Wattlebrook Lane Melbourne Vic 3000

ABN 38 614 207 923
Tel: +61 0487 259 318 | Email: dale.morven@plivorantu.com

Font styles to use
Decorative
Script

Requirements
Must have
• Try few different design and some round corner business card
Should not have
• One round corner business card...try 4 different colour background not only black, make sure two side is designed. Be creative so imagine you are giving this to a client make sure has wow factor, if you can also try one design with engrave like all the logo, words look 3d feel
• The word Advertising Platform use attached file font

```html
<!DOCTYPE html>
<html lang="en">
<head>
<meta charset="utf-8">
<title>Kestrelle Loop – Business Card</title>
<link rel="stylesheet" href="https://fonts.googleapis.com/css2?family=Roboto:wght@400;500;700&display=swap">
<style>
  :root {
    --page-bg: #2b2b2b;
    --card-bg: #2a2828;
    --card-edge: #3a3737;
    --text-light: #f2f2f2;
    --text-soft: #cfcfcf;
    --accent-orange: #f0602a;
    --accent-amber: #f39a3a;
    --accent-teal: #2fb8a8;
  }
  * { margin: 0; padding: 0; box-sizing: border-box; }
  html, body {
    width: 1200px; height: 886px; overflow: hidden;
    background: var(--page-bg);
    font-family: "Roboto", Arial, sans-serif;
  }
  .canvas { position: relative; width: 1200px; height: 886px; }

  .card {
    position: absolute;
    width: 540px; height: 324px;
    background: var(--card-bg);
    border: 1px solid var(--card-edge);
    border-radius: 26px;
    overflow: hidden;
    box-shadow: 0 14px 34px rgba(0,0,0,.45);
  }
  .card-front { left: 70px; top: 120px; }
  .card-back  { left: 590px; top: 442px; }

  /* front */
  .brand {
    position: absolute; left: 0; right: 0; top: 100px;
    display: flex; align-items: center; justify-content: center; gap: 16px;
  }
  .brand-dot {
    width: 54px; height: 54px; border-radius: 50%;
    background: var(--accent-orange);
  }
  .brand-name {
    font-size: 40px; font-weight: 700; color: var(--accent-orange);
    letter-spacing: 1px;
  }
  .website {
    position: absolute; left: 0; right: 0; top: 236px;
    text-align: center;
    font-size: 14px; letter-spacing: 6px; color: var(--text-soft);
  }

  /* back */
  .name-band {
    position: absolute; left: 0; top: 28px;
    width: 300px; height: 98px;
    padding: 14px 0 0 56px;
    background: linear-gradient(90deg, var(--accent-orange), var(--accent-amber));
    border-radius: 0 12px 12px 0;
    color: var(--text-light);
  }
  .person-name { font-size: 20px; font-weight: 700; text-transform: uppercase; }
  .person-role { font-size: 14px; font-weight: 500; text-transform: uppercase; line-height: 1.3; margin-top: 2px; }

  .details {
    position: absolute; left: 56px; top: 150px;
    color: var(--text-light); font-size: 15px; line-height: 1.35;
  }
  .contact-row { display: flex; align-items: center; gap: 8px; margin-left: -22px; }
  .contact-row svg { width: 14px; height: 14px; flex: none; }

  .brand-watermark {
    position: absolute; right: 44px; top: 70px;
    width: 190px; height: 190px; border-radius: 50%;
    background: var(--accent-orange); opacity: .18;
  }
</style>
</head>
<body>
<main class="canvas">

  <section class="card card-front" aria-label="Card front">
    <div class="brand">
      <span class="brand-dot"></span>
      <span class="brand-name">Kestrelle Loop</span>
    </div>
    <p class="website">www.plivorantu.com</p>
  </section>

  <section class="card card-back" aria-label="Card back">
    <div class="brand-watermark"></div>
    <div class="name-band">
      <p class="person-name">Dale Morven</p>
      <p class="person-role">Co-Founder<br>Managing Director</p>
    </div>
    <div class="details">
      <p>Plivorantu</p>
      <p>ABN 38 614 207 923</p>
      <p>Suite 718 240 Wattlebrook Lane</p>
      <p>Melbourne Vic 3000</p>
      <p class="contact-row">
        <svg viewBox="0 0 24 24" aria-hidden="true"><path fill="var(--accent-orange)" d="M6.6 10.8a15.1 15.1 0 0 0 6.6 6.6l2.2-2.2a1 1 0 0 1 1-.25 11.4 11.4 0 0 0 3.6.57 1 1 0 0 1 1 1V20a1 1 0 0 1-1 1A17 17 0 0 1 3 4a1 1 0 0 1 1-1h3.5a1 1 0 0 1 1 1c0 1.25.2 2.45.57 3.57a1 1 0 0 1-.25 1z"/></svg>
        +61 0487 259 318
      </p>
      <p class="contact-row">
        <svg viewBox="0 0 24 24" aria-hidden="true"><rect x="2" y="5" width="20" height="14" rx="2" fill="var(--accent-orange)"/><path d="M3 6l9 7 9-7" fill="none" stroke="var(--card-bg)" stroke-width="1.8"/></svg>
        dale.morven@plivorantu.com
      </p>
    </div>
  </section>

</main>
</body>
</html>
```